TALMORK

The business want a professional looking business card. We have a scetch we will add but want the extra upgrade, and would like more suggestions for variations of our business cards.

```html
<!DOCTYPE html>
<html lang="en">
<head>
<meta charset="utf-8">
<title>TALMORK Business Card</title>
<link rel="stylesheet" href="https://fonts.googleapis.com/css2?family=Montserrat:wght@400;500;700&display=swap">
<style>
  :root {
    --page: #151515;
    --card: #1e1e1e;
    --card-edge: #262626;
    --gold: #c9a257;
    --gold-light: #e6c77c;
    --gold-dark: #8c6a2c;
    --text: #f2f2f2;
  }
  * { box-sizing: border-box; margin: 0; padding: 0; }
  html, body { width: 1200px; height: 1059px; overflow: hidden; background: var(--page); }
  body { position: relative; font-family: "Montserrat", sans-serif; }

  .card {
    position: absolute;
    background: var(--card);
    border-radius: 16px;
    overflow: hidden;
  }
  .card-front { left: 257px; top: 89px; width: 687px; height: 390px; }
  .card-back  { left: 254px; top: 546px; width: 693px; height: 394px; }

  .brand { position: absolute; left: 35px; top: 56px; width: 320px; text-align: center; }
  .brand-name {
    font-weight: 500; font-size: 44px; letter-spacing: 12px;
    color: var(--gold); line-height: 1;
  }
  .brand-since {
    margin-top: 14px; font-weight: 700; font-size: 13px;
    letter-spacing: 9px; color: var(--gold);
  }

  .accent-bar { position: absolute; left: 0; top: 176px; width: 20px; height: 42px; background: linear-gradient(var(--gold), var(--gold-dark)); }

  .person { position: absolute; left: 41px; top: 172px; }
  .person-name { font-weight: 700; font-size: 23px; color: var(--gold); line-height: 1.2; }
  .person-title { font-weight: 400; font-size: 18px; color: var(--text); line-height: 1.4; }

  .contacts { position: absolute; left: 38px; top: 258px; list-style: none; }
  .contacts li { display: flex; align-items: center; height: 34px; font-size: 19px; color: var(--text); }
  .contacts svg { width: 16px; height: 16px; margin-right: 10px; flex: none; }

  .mark-decoration {
    position: absolute; left: 387px; top: 33px; width: 290px; height: 290px;
    background: radial-gradient(circle, #2c2c2c 0%, #232323 45%, rgba(30,30,30,0) 70%);
  }

  .swoosh { position: absolute; left: 0; bottom: 0; width: 687px; height: 45px; }

  .pattern-field {
    position: absolute; inset: 0;
    background:
      radial-gradient(ellipse 120px 105px at 79% 59%, var(--card) 80%, rgba(30,30,30,0) 100%),
      linear-gradient(100deg, #141414 0%, #1c1c1c 40%, #3a3a3a 75%, #4a4a4a 100%);
  }
  .back-brand { position: absolute; left: 465px; top: 250px; width: 160px; text-align: center; }
  .back-brand .brand-name { font-size: 22px; letter-spacing: 5px; }
  .back-brand .brand-since { margin-top: 6px; font-size: 7px; letter-spacing: 4px; }
  .back-dot { display: block; width: 22px; height: 22px; border-radius: 50%; background: var(--gold); margin: 0 auto 14px; }
</style>
</head>
<body>

<section class="card card-front">
  <div class="brand">
    <div class="brand-name">TALMORK</div>
    <div class="brand-since">SINCE 2026</div>
  </div>

  <div class="accent-bar"></div>

  <div class="person">
    <div class="person-name">Erik Holm Sandvik</div>
    <div class="person-title">CEO &amp; Founder</div>
  </div>

  <ul class="contacts">
    <li>
      <svg viewBox="0 0 16 16"><path fill="#c9a257" d="M4 1.5 6 4.5 4.8 6c.8 1.9 2.3 3.4 4.2 4.2L10.5 9l3 2-1.3 2.7c-5.5-.4-9.8-4.7-10.2-10.2z"/></svg>
      004795551208
    </li>
    <li>
      <svg viewBox="0 0 16 16"><path fill="#c9a257" d="M1 5l7-4 7 4v9H1z"/><path fill="#1e1e1e" d="M2.5 6.5 8 10l5.5-3.5v6h-11z"/></svg>
      talmork.llc@mailhub.com
    </li>
    <li>
      <svg viewBox="0 0 16 16"><circle cx="8" cy="8" r="7" fill="#c9a257"/><path fill="#1e1e1e" d="M5 4c2 0 2 2 3 2s1 2-1 2-2 2-1 4c-2-1-3-3-3-5 0-1 1-3 2-3zM11 9c1 0 2 1 1 2s-2 1-2 0 0-2 1-2z"/></svg>
      www.talmork.llc
    </li>
  </ul>

  <div class="mark-decoration" role="img" aria-label="Large embossed brand mark decoration"></div>

  <svg class="swoosh" viewBox="0 0 687 45" preserveAspectRatio="none">
    <defs>
      <linearGradient id="gold-sweep" x1="0" x2="1">
        <stop offset="0" stop-color="#8c6a2c"/>
        <stop offset="0.45" stop-color="#e6c77c"/>
        <stop offset="1" stop-color="#9c7635"/>
      </linearGradient>
    </defs>
    <path d="M150 45 C300 15 500 2 687 0 L687 3 C500 5 320 20 200 45 Z" fill="url(#gold-sweep)"/>
    <path d="M235 45 C380 18 540 8 687 5 L687 45 Z" fill="url(#gold-sweep)"/>
  </svg>
</section>

<section class="card card-back">
  <div class="pattern-field" role="img" aria-label="Repeating embossed brand mark pattern fading from black to silver"></div>
  <div class="back-brand">
    <span class="back-dot"></span>
    <div class="brand-name">TALMORK</div>
    <div class="brand-since">SINCE 2026</div>
  </div>
</section>

</body>
</html>
```